Design and Renovation Company Luxury Business Card

I want to create a luxury business card for a Design and Renovation Firm . We will use our current logo. The company name is 528BUILDA. We do not want anything standard. We need a very unique concept.
Please see uploaded inspiration. I really like the textured paper option. I would like the card to be thick with debossing, and/or embossing options. The logo has orange in it but I would like to see the card with and without the orange. I think the orange may make the company feel less high-end. The goal is to elevate the logo not match its vibe per se of the logo. We want something very unique, not standard at all!
I would like a space for :
Logo,
Name,
Position,
Email,
Office number,
Website Address,
Business Address,
Thank you!
Have fun!
Target Market(s)
Home owners Age 35 +
Industry/Entity Type
Design and Renovation
Contact Information for Business Card
Logo, Name, Position, Email, Office number, Website Address, Business Address,.
Colors
Designer to choose colors to be used in the design.
Requirements
Must have
- A luxury designer feel. Must be black or dark grey but open to other luxury ideas.
Nice to have
- Gold, silver, black embossing or debossing. Textured paper design.
Should not have
- A cheap look and feel.

```html
<!DOCTYPE html>
<html lang="en">
<head>
<meta charset="utf-8">
<title>528BUILDA Business Card</title>
<link rel="stylesheet" href="https://fonts.googleapis.com/css2?family=Poppins:wght@400;500;600&display=swap">
<style>
  :root {
    --backdrop: #d3d7d8;
    --card: #222226;
    --ink: #ffffff;
    --tile-light: #e6e6e6;
    --tile-mid: #5a5b60;
    --tile-dark: #17181b;
    --card-radius: 167px;
  }
  * { margin: 0; padding: 0; box-sizing: border-box; }
  html, body { width: 1200px; height: 960px; overflow: hidden; }
  body {
    background: var(--backdrop);
    font-family: "Poppins", sans-serif;
    color: var(--ink);
    position: relative;
  }
  .card {
    position: absolute;
    top: 105px;
    width: 431px;
    height: 750px;
    box-shadow: 0 14px 26px rgba(0, 0, 0, 0.28);
  }
  .card-back {
    left: 142px;
    border-radius: var(--card-radius) 0 var(--card-radius) 0;
    background:
      radial-gradient(ellipse 90% 55% at 10% 10%, var(--tile-light) 0%, rgba(150,150,155,0.7) 30%, rgba(40,41,45,0) 70%),
      linear-gradient(160deg, var(--tile-mid) 0%, var(--tile-dark) 60%, #0e0f11 100%);
  }
  .card-front {
    left: 630px;
    background: var(--card);
    border-radius: 0 var(--card-radius) 0 var(--card-radius);
  }
  .brand-name {
    position: absolute;
    top: 72px;
    left: 58px;
    font-size: 44px;
    font-weight: 500;
    line-height: 1;
  }
  .person {
    position: absolute;
    top: 421px;
    left: 0;
    width: 100%;
    text-align: center;
  }
  .person-name { font-size: 37px; line-height: 1.2; }
  .person-name .first { font-weight: 600; }
  .person-name .last { font-weight: 400; }
  .person-role { font-size: 19px; font-weight: 500; margin-top: 2px; }
  .address {
    position: absolute;
    top: 522px;
    left: 70px;
    font-size: 19.5px;
    line-height: 27px;
    letter-spacing: 0.3px;
  }
  .contacts {
    position: absolute;
    top: 604px;
    left: 70px;
    list-style: none;
    font-size: 19.5px;
    letter-spacing: 0.3px;
  }
  .contacts li {
    display: flex;
    align-items: center;
    height: 27.5px;
  }
  .contacts svg { width: 18px; height: 18px; margin-right: 13px; fill: var(--ink); }
</style>
</head>
<body>
  <div class="card card-back" role="img" aria-label="Glossy black mosaic tile pattern fading to white tiles at the top left"></div>

  <div class="card card-front">
    <p class="brand-name">528BUILDA</p>

    <div class="person">
      <p class="person-name"><span class="first">Marena</span> <span class="last">Volkova</span></p>
      <p class="person-role">Founder &amp; CEO</p>
    </div>

    <p class="address">1840 Linden Ave. Suite 300<br>Arlington, TX 76011</p>

    <ul class="contacts">
      <li>
        <svg viewBox="0 0 24 24" aria-hidden="true"><path d="M6.6 10.8a15.1 15.1 0 0 0 6.6 6.6l2.2-2.2a1 1 0 0 1 1-.25 11.4 11.4 0 0 0 3.6.57 1 1 0 0 1 1 1V20a1 1 0 0 1-1 1A17 17 0 0 1 3 4a1 1 0 0 1 1-1h3.5a1 1 0 0 1 1 1c0 1.25.2 2.450.57 3.57a1 1 0 0 1-.25 1z"/></svg>
        (817) 555-0142
      </li>
      <li>
        <svg viewBox="0 0 24 24" aria-hidden="true"><path d="M12 2a10 10 0 1 0 0 20 10 10 0 0 0 0-20zm6.9 6h-3a15.6 15.6 0 0 0-1.4-3.6A8 8 0 0 1 18.9 8zM12 4c.8 1.2 1.5 2.5 1.9 4h-3.8c.4-1.5 1.1-2.8 1.9-4zM4.3 14a8 8 0 0 1 0-4h3.4a16.5 16.5 0 0 0 0 4zm.8 2h3a15.6 15.6 0 0 0 1.4 3.6A8 8 0 0 1 5.1 16zm3-8h-3a8 8 0 0 1 4.4-3.6A15.6 15.6 0 0 0 8.1 8zM12 20c-.8-1.2-1.5-2.5-1.9-4h3.8c-.4 1.5-1.1 2.8-1.9 4zm2.3-6H9.7a14.7 14.7 0 0 1 0-4h4.6a14.7 14.7 0 0 1 0 4zm.2 5.6a15.6 15.6 0 0 0 1.4-3.6h3a8 8 0 0 1-4.4 3.6zm1.8-5.6a16.5 16.5 0 0 0 0-4h3.4a8 8 0 0 1 0 4z"/></svg>
        info@yourwebsite.com
      </li>
      <li>
        <svg viewBox="0 0 24 24" aria-hidden="true"><path d="M2 9l10-7 10 7v12H2zm2 1.3V19h16v-8.7l-8 5.5z"/></svg>
        www.yourwebsite.com
      </li>
    </ul>
  </div>
</body>
</html>
```